Quillbrook IT company focused on 3 areas of IT

Looking for something similar to attached cards. Logo for quillbrook also attached.. Looking for something clean as far as colors (surprise me).. Quill stands for 3 primary areas, web design, consulting and network infrastructure design. Please email me if you have any questions. Looking forward to seeing how creative and professional this card will look. Thank you,

Target Market(s)

Small business/consumers looking for It services

Industry/Entity Type

It Service

Contact Information for Business Card

Dorin Vasek
Principal Consultant

202-555-0173

www.quillbrook-example.com
dvasek@quillbrook-example.com

27416 Copper Lantern Way,
Larkfield, VA 20999

Colors

Designer to choose colors to be used in the design.

Requirements
Must have
• attached Logo design. Feel free to play with the colors.. If you have a better idea for a card, please fee free to send me. Looking for something clean/modern. Should have tech feel, not cheesy.
Nice to have
• Surprise me :-)..

```html
<!DOCTYPE html>
<html lang="en">
<head>
<meta charset="utf-8">
<title>Quillbrook — Business Card</title>
<link rel="stylesheet" href="https://fonts.googleapis.com/css2?family=Oswald:wght@500&family=Work+Sans:wght@400;600&display=swap">
<style>
  :root {
    --backdrop: #1c1c1c;
    --card: #161616;
    --card-edge: #222222;
    --foil: #e6e6e6;
    --foil-soft: #cfcfcf;
    --gloss: #0a0a0a;
    --gloss-line: #2a2a2a;
    --muted: #2e2e2e;
  }
  * { box-sizing: border-box; margin: 0; padding: 0; }
  html, body {
    width: 1200px; height: 900px; overflow: hidden;
    background: var(--backdrop);
  }
  .canvas {
    position: relative; width: 1200px; height: 900px;
    background: var(--backdrop);
  }
  .card {
    position: absolute; left: 250px; width: 700px; height: 400px;
    background: linear-gradient(135deg, #1a1a1a 0%, var(--card) 55%, #121212 100%);
    border: 1px solid var(--card-edge);
  }
  .card--front { top: 40px; }
  .card--back { top: 460px; }

  .brand-name {
    position: absolute; left: 0; right: 0; top: 170px;
    text-align: center;
    font-family: "Work Sans", sans-serif; font-weight: 600;
    font-size: 46px; letter-spacing: 1px;
    color: var(--foil);
  }

  .identity {
    position: absolute; left: 90px; top: 150px;
  }
  .identity__name {
    font-family: "Oswald", sans-serif; font-weight: 500;
    font-size: 34px; letter-spacing: 5px; line-height: 1;
    color: var(--gloss);
    text-shadow: 0 1px 0 var(--gloss-line), 0 -1px 0 #050505;
    text-transform: uppercase;
    white-space: nowrap;
  }
  .identity__title {
    margin-top: 4px;
    font-family: "Work Sans", sans-serif; font-weight: 600;
    font-size: 15px; letter-spacing: 0.5px;
    color: var(--muted);
  }
  .divider {
    position: absolute; left: 344px; top: 148px;
    width: 1px; height: 66px; background: var(--muted);
  }
  .contacts {
    position: absolute; left: 364px; top: 146px;
    list-style: none;
  }
  .contacts__item {
    display: flex; align-items: center; gap: 10px;
    height: 23px;
    font-family: "Work Sans", sans-serif; font-weight: 400;
    font-size: 16px; letter-spacing: 0.5px;
    color: var(--foil-soft);
    white-space: nowrap;
  }
  .contacts__icon { width: 11px; height: 11px; flex: none; }
  .address {
    position: absolute; left: 90px; top: 318px;
    font-family: "Work Sans", sans-serif; font-weight: 400;
    font-size: 16px; letter-spacing: 0.8px;
    color: var(--foil-soft);
    white-space: nowrap;
  }
  .address__street { color: var(--gloss); text-shadow: 0 1px 0 var(--gloss-line); }
</style>
</head>
<body>
<main class="canvas">
  <section class="card card--front">
    <div class="brand-name">Quillbrook</div>
  </section>

  <section class="card card--back">
    <div class="identity">
      <div class="identity__name">Dorin Vasek</div>
      <div class="identity__title">Principal Consultant</div>
    </div>
    <div class="divider"></div>
    <ul class="contacts">
      <li class="contacts__item">
        <svg class="contacts__icon" viewBox="0 0 12 12" aria-hidden="true">
          <path d="M2.5 1 L4.5 1 L5.2 3.5 L4 4.5 Q5 7 7.5 8 L8.5 6.8 L11 7.5 L11 9.5 Q10.5 11 9 11 Q1 10 1 3 Q1 1.5 2.5 1 Z" fill="#cfcfcf"/>
        </svg>202-555-0173
      </li>
      <li class="contacts__item">
        <svg class="contacts__icon" viewBox="0 0 12 12" aria-hidden="true">
          <rect x="0.75" y="2.25" width="10.5" height="7.5" fill="none" stroke="#cfcfcf" stroke-width="1.2"/>
          <path d="M1 2.6 L6 6.6 L11 2.6" fill="none" stroke="#cfcfcf" stroke-width="1.2"/>
        </svg>dvasek@quillbrook-example.com
      </li>
      <li class="contacts__item">
        <svg class="contacts__icon" viewBox="0 0 12 12" aria-hidden="true">
          <circle cx="6" cy="6" r="5" fill="none" stroke="#cfcfcf" stroke-width="1.1"/>
          <ellipse cx="6" cy="6" rx="2.2" ry="5" fill="none" stroke="#cfcfcf" stroke-width="1"/>
          <path d="M1 6 H11" stroke="#cfcfcf" stroke-width="1"/>
        </svg>www.quillbrook-example.com
      </li>
    </ul>
    <div class="address"><span class="address__street">27416 Copper Lantern Way,</span> Larkfield, VA 20999</div>
  </section>
</main>
</body>
</html>
```